i need a business card for a plumbing company in california

we are a drain cleaning , maintenance plumbing company who is starting new marketing campaign for a tatrench-less pipe installation department .

Target Market(s)

the professional who appreciates time and quality workmanship.

Industry/Entity Type

Plumbing

Colors
0655a3
ec1f27

Requirements
Must have
• the second logo needs to be included
Nice to have
• a focus on the services offered
Should not have
• any underlined words on the brief

```html
<!DOCTYPE html>
<html lang="en">
<head>
<meta charset="utf-8">
<title>Pipewell Plumbing – Business Card</title>
<link rel="stylesheet" href="https://fonts.googleapis.com/css2?family=Arimo:wght@400;700&display=swap">
<style>
  :root {
    --brand-blue: #0655a3;
    --brand-blue-deep: #06397a;
    --brand-red: #ec1f27;
    --card-white: #f7f7f7;
    --logo-grey: #6b6b63;
    --backdrop: #2e2e2e;
    --text-light: #ffffff;
  }
  * { box-sizing: border-box; margin: 0; padding: 0; }
  html, body {
    width: 1200px;
    height: 997px;
    overflow: hidden;
    background: var(--backdrop);
    font-family: "Arimo", Arial, sans-serif;
  }
  .canvas {
    position: relative;
    width: 1200px;
    height: 997px;
  }
  .card {
    position: absolute;
    top: 348px;
    width: 520px;
    height: 300px;
    border-radius: 16px;
    overflow: hidden;
    box-shadow: 0 14px 30px rgba(0,0,0,0.45);
  }
  .card--front { left: 53px; }
  .card--back { left: 627px; }
  .card__art {
    position: absolute;
    inset: 0;
    width: 100%;
    height: 100%;
  }
  .brand-name {
    position: absolute;
    font-weight: 700;
    font-size: 36px;
    line-height: 0.95;
    letter-spacing: -0.5px;
  }
  .card--front .brand-name {
    left: 48px;
    top: 40px;
    color: var(--text-light);
  }
  .card--back .brand-name {
    left: 150px;
    top: 42px;
    color: var(--logo-grey);
  }
  .services {
    position: absolute;
    left: 20px;
    bottom: 22px;
    font-weight: 700;
    font-size: 12.5px;
    letter-spacing: 0.3px;
    color: var(--brand-red);
    white-space: nowrap;
  }
  .services__accent { color: var(--brand-blue); }
  .contact-person {
    position: absolute;
    left: 80px;
    top: 226px;
    text-align: center;
  }
  .contact-person__name {
    font-weight: 700;
    font-size: 16px;
    color: var(--brand-red);
    letter-spacing: 0.5px;
  }
  .contact-person__role {
    font-size: 13px;
    color: var(--text-light);
    margin-top: 2px;
  }
  .divider {
    position: absolute;
    left: 292px;
    top: 200px;
    width: 1px;
    height: 70px;
    background: rgba(255,255,255,0.55);
  }
  .contact-list {
    position: absolute;
    left: 312px;
    top: 196px;
    list-style: none;
    font-size: 12.5px;
    color: var(--text-light);
  }
  .contact-list li {
    display: flex;
    align-items: center;
    gap: 7px;
    height: 24px;
  }
  .contact-list svg { width: 13px; height: 13px; flex: none; }
  .contact-list__web {
    font-weight: 700;
    color: var(--brand-red);
    letter-spacing: 0.3px;
  }
</style>
</head>
<body>
<main class="canvas">

  <section class="card card--front" aria-label="Business card front">
    <svg class="card__art" viewBox="0 0 520 300" preserveAspectRatio="none" aria-hidden="true">
      <defs>
        <linearGradient id="front-blue" x1="0" y1="0" x2="0" y2="1">
          <stop offset="0" stop-color="#0a5fb0"/>
          <stop offset="1" stop-color="#06397a"/>
        </linearGradient>
      </defs>
      <rect width="520" height="300" fill="url(#front-blue)"/>
      <path d="M0,235 C130,215 200,140 330,120 C420,106 480,100 520,96 L520,300 L0,300 Z" fill="#f7f7f7"/>
      <path d="M0,220 C130,198 200,122 330,102 C420,88 480,84 520,82 L520,92 C480,96 420,102 330,116 C200,136 130,212 0,232 Z" fill="#ec1f27"/>
    </svg>
    <p class="brand-name">Pipewell<br>Plumbing</p>
    <p class="services">SEWER DRAIN CLEANING, <span class="services__accent">MAINTENANCE,</span> TRENCHLESS PIPE INSTALLS</p>
  </section>

  <section class="card card--back" aria-label="Business card back">
    <svg class="card__art" viewBox="0 0 520 300" preserveAspectRatio="none" aria-hidden="true">
      <defs>
        <linearGradient id="back-blue" x1="0" y1="0" x2="0" y2="1">
          <stop offset="0" stop-color="#0a5aa8"/>
          <stop offset="1" stop-color="#06397a"/>
        </linearGradient>
      </defs>
      <rect width="520" height="300" fill="#f7f7f7"/>
      <path d="M0,196 C120,222 230,196 330,158 C420,124 480,118 520,116 L520,300 L0,300 Z" fill="url(#back-blue)"/>
      <path d="M0,178 C120,206 230,178 330,140 C420,108 480,102 520,100 L520,110 C480,112 420,118 330,150 C230,188 120,214 0,190 Z" fill="#ec1f27"/>
    </svg>
    <p class="brand-name">Pipewell<br>Plumbing</p>
    <div class="contact-person">
      <p class="contact-person__name">MARCO DELGADO</p>
      <p class="contact-person__role">Director</p>
    </div>
    <span class="divider"></span>
    <ul class="contact-list">
      <li>
        <svg viewBox="0 0 16 16" aria-hidden="true"><circle cx="8" cy="8" r="7.5" fill="none" stroke="#fff"/><path d="M5 5.5c0 3 2.5 5.5 5.5 5.5l.8-1.4-1.6-.8-.7.7c-1-.4-1.8-1.2-2.2-2.2l.7-.7-.8-1.6z" fill="#fff"/></svg>
        <span>1300555019</span>
      </li>
      <li>
        <svg viewBox="0 0 16 16" aria-hidden="true"><circle cx="8" cy="8" r="7.5" fill="none" stroke="#fff"/><rect x="4" y="5.5" width="8" height="5.5" fill="none" stroke="#fff"/><path d="M4 5.5l4 3 4-3" fill="none" stroke="#fff"/></svg>
        <span>hello@pipewellplumbing.com</span>
      </li>
      <li class="contact-list__web">www.pipewellplumbing.com</li>
    </ul>
  </section>

</main>
</body>
</html>
```